New Baby product needs fun and creative design

We are about to launch are new product for babies and we need some amazing packaging, the product is a snot sucker for blocked noses also known as a nasal aspirator, We are looking for a Creative with a Capital C packaging, we want a nice concept on the box an illustration of a baby and mum using the product like pic attached (example 1) or maybe an illustration of a baby with the pipe, the design has to be new and up to date, I am looking for an animated type feel. Something that make it look baby friendly and comfortable

The packaging is a rectangular box

The colours should be matched with the logo(Baby PIXU) but if not it is still fine as long as there is not a big contrast

Full text for the box will be provided for back and front, the main design will be for the front of the box

Target Market(s)

Mum's with new born babies

Industry/Entity Type

Baby

Requirements
Must have
• Illustration of showing a mum and baby like the example 1
Nice to have
• An animated illustration of a mother and baby using the product or a baby with the pipe in it's nose, something that would look friendly and welcoming for mums
Should not have
• solid colours and medicine like aligned instructional text on the front. Old style designs, should be in line with current designs similar to picture shown

```html
<!DOCTYPE html>
<html lang="en">
<head>
<meta charset="utf-8">
<title>Baby PIXU Nasal Aspirator – Box Panels</title>
<link href="https://fonts.googleapis.com/css2?family=Fredoka:wght@500;600;700&family=Arvo:ital,wght@1,700&family=Roboto:wght@400;700&display=swap" rel="stylesheet">
<style>
  :root {
    --stage: #7f9cc3;
    --stage-light: #c9d5e6;
    --sky: #b6e2f0;
    --blush: #f2c3da;
    --brand-pink: #d9539a;
    --brand-purple: #4b3c8e;
    --side-dark: #3a2f78;
    --side-mid: #4d3f92;
    --heading-cyan: #6fd0e6;
    --bullet-orange: #f07a2a;
    --ring-pink: #e7a6c9;
    --ring-grey: #b9babd;
    --skin-light: #ecd6c8;
    --skin-dark: #c48f74;
    --ink: #4a4150;
    --white: #ffffff;
  }
  * { box-sizing: border-box; margin: 0; padding: 0; }
  html, body { width: 1200px; height: 1200px; overflow: hidden; }
  body {
    background: linear-gradient(180deg, var(--stage) 0%, var(--stage-light) 100%);
    display: flex; align-items: center; justify-content: center;
    font-family: "Roboto", Arial, sans-serif;
  }
  .box-net { display: flex; height: 1000px; box-shadow: 0 20px 50px rgba(30,30,70,.25); }
  .side-panel {
    width: 260px; height: 1000px;
    background: linear-gradient(180deg, var(--side-mid) 0%, var(--side-dark) 100%);
    color: var(--white);
    padding: 40px 26px;
  }
  .side-logo {
    display: flex; align-items: center; gap: 8px;
    font-family: "Fredoka", sans-serif; font-weight: 600; font-size: 22px;
    color: #bfe6f2; margin-bottom: 110px;
  }
  .side-logo .dot { width: 14px; height: 14px; border-radius: 50%; background: #bfe6f2; }
  .side-heading { color: var(--heading-cyan); font-weight: 700; font-size: 17px; margin: 0 0 12px; }
  .contents-list { list-style: none; margin-bottom: 70px; }
  .contents-list li { font-size: 16px; line-height: 28px; display: flex; align-items: center; gap: 10px; }
  .contents-list li::before { content: ""; width: 8px; height: 8px; background: var(--bullet-orange); }
  .side-copy { font-size: 16px; line-height: 30px; margin-bottom: 14px; }
  .front-panel { width: 520px; height: 1000px; display: block; }
</style>
</head>
<body>
  <div class="box-net">
    <section class="side-panel">
      <div class="side-logo"><span class="dot"></span>Baby PIXU</div>

      <h2 class="side-heading">This box Contains:</h2>
      <ul class="contents-list">
        <li>Suction Pipe</li>
        <li>Replaceable Heads</li>
        <li>Sanitary Box</li>
      </ul>

      <h2 class="side-heading">Directions for Use:</h2>
      <p class="side-copy">Gently position the end of the tubing into the edge of baby's nostril. Using the mouth piece attached gently suction mucus out of baby's nostril and into the nozzle.</p>
      <p class="side-copy">After Use: Rinse aspirator with warm soapy water and return to sanitary box ready for the next use.</p>

      <h2 class="side-heading">Please note:</h2>
      <p class="side-copy">Once opened, remove inner white plastic from the sanitary box.</p>
    </section>

    <svg class="front-panel" viewBox="0 0 520 1000" xmlns="http://www.w3.org/2000/svg">
      <defs>
        <linearGradient id="front-bg" x1="0" y1="0" x2="0" y2="1">
          <stop offset="0" stop-color="var(--sky)"/>
          <stop offset="0.55" stop-color="#dfe3f0"/>
          <stop offset="1" stop-color="var(--blush)"/>
        </linearGradient>
        <radialGradient id="baby-art" cx="0.6" cy="0.35" r="0.8">
          <stop offset="0" stop-color="var(--skin-light)"/>
          <stop offset="1" stop-color="var(--skin-dark)"/>
        </radialGradient>
        <clipPath id="panel-clip"><rect width="520" height="1000"/></clipPath>
        <path id="tagline-arc" d="M264.6 445.2 A335 335 0 0 1 464.8 874.6"/>
      </defs>

      <g clip-path="url(#panel-clip)">
        <rect class="front-background" width="520" height="1000" fill="url(#front-bg)"/>

        <g class="brand-tab">
          <rect x="185" y="-12" width="150" height="84" rx="12" fill="var(--white)"/>
          <circle cx="208" cy="38" r="7" fill="var(--brand-pink)"/>
          <text x="222" y="45" font-family="Fredoka, sans-serif" font-weight="600" font-size="20" fill="var(--brand-pink)">Baby PIXU</text>
        </g>

        <text class="product-title" x="260" y="250" text-anchor="middle" textLength="470" lengthAdjust="spacingAndGlyphs"
              font-family="Fredoka, sans-serif" font-weight="700" font-size="64"
              stroke="var(--white)" stroke-width="6" paint-order="stroke" stroke-linejoin="round">
          <tspan fill="var(--brand-purple)">NASAL</tspan><tspan fill="var(--brand-pink)"> ASPIRATOR</tspan>
        </text>

        <g class="badge-circle">
          <circle cx="150" cy="760" r="380" fill="none" stroke="var(--ring-pink)" stroke-width="18"/>
          <circle cx="150" cy="760" r="371" fill="var(--white)" opacity="0.9"/>
          <circle cx="150" cy="760" r="316" fill="none" stroke="var(--ring-grey)" stroke-width="12"/>
          <circle cx="150" cy="760" r="308" fill="url(#baby-art)" role="img" aria-label="Illustration of a smiling cartoon baby face with a curl of hair"/>
          <text class="tagline" font-family="Arvo, serif" font-style="italic" font-weight="700" font-size="22" fill="var(--ink)">
            <textPath href="#tagline-arc">Gently clear baby's blocked nose in seconds</textPath>
          </text>
        </g>
      </g>
    </svg>
  </div>
</body>
</html>
```